BrimFalcon Business Cards

We have a defined brand. Please visit our website to get a feel for the product and the color pallets. www.brimfalcon-example.com

We need an updated, world class business card design. (See the attached existing card design). Please utilize BOTH sides of the card as shown and be creative with the layout. I do want the horse head icon to be positioned as it is with the existing card.

The remainder of the layout can be customized and I also want it vertically oriented.

Attached are the logo files and please use the colors as follows:
Green - #A5CE39
Tan - #CDBD99
Black

Feel free to play with the colors.

```html
<!DOCTYPE html>
<html lang="en">
<head>
<meta charset="utf-8">
<title>BrimFalcon Business Cards</title>
<link href="https://fonts.googleapis.com/css2?family=Exo+2:wght@500&family=Montserrat:wght@300;400;500&display=swap" rel="stylesheet">
<style>
  :root {
    --bg: #d9d9d7;
    --card-white: #ffffff;
    --card-dark: #2f2f31;
    --edge-green: #2f9a3c;
    --brand-green: #a5ce39;
    --deep-green: #5b9a2f;
    --ink: #111111;
    --grey-text: #6d6d6d;
    --white: #ffffff;
  }
  html, body {
    margin: 0;
    width: 1200px;
    height: 801px;
    overflow: hidden;
    background: var(--bg);
  }
  .stage {
    position: relative;
    width: 1200px;
    height: 801px;
  }
  .card {
    position: absolute;
    top: 230px;
    width: 540px;
    height: 310px;
    box-sizing: border-box;
    border-bottom: 3px solid var(--edge-green);
    box-shadow: 0 6px 18px rgba(0,0,0,0.18);
  }
  .card-front {
    left: 40px;
    background: var(--card-white);
  }
  .card-back {
    left: 620px;
    background: var(--card-dark);
    display: flex;
    align-items: center;
    justify-content: center;
  }
  .brand {
    display: flex;
    align-items: center;
    gap: 10px;
  }
  .brand-dot {
    width: 28px;
    height: 28px;
    border-radius: 50%;
    background: var(--ink);
  }
  .brand-name {
    font-family: "Exo 2", sans-serif;
    font-weight: 500;
    font-size: 34px;
    letter-spacing: 1px;
    color: var(--ink);
    line-height: 1;
  }
  .card-back .brand-dot { background: var(--white); width: 40px; height: 40px; }
  .card-back .brand-name { color: var(--white); font-size: 48px; }
  .front-info {
    position: absolute;
    left: 30px;
    top: 28px;
    font-family: "Montserrat", sans-serif;
  }
  .tagline {
    margin: 4px 0 0 38px;
    font-size: 11px;
    letter-spacing: 3px;
    color: var(--ink);
  }
  .person-name {
    margin: 26px 0 0;
    font-size: 20px;
    font-weight: 500;
    letter-spacing: 0.5px;
    color: var(--brand-green);
    background: linear-gradient(90deg, var(--brand-green), var(--deep-green));
    -webkit-background-clip: text;
    background-clip: text;
  }
  .person-role {
    margin: 2px 0 0;
    font-size: 14px;
    font-weight: 300;
    color: var(--grey-text);
  }
  .address {
    margin: 16px 0 0;
    font-size: 13px;
    font-weight: 300;
    line-height: 1.4;
    color: var(--grey-text);
  }
  .contact {
    list-style: none;
    margin: 16px 0 0;
    padding: 0;
    font-size: 13px;
    font-weight: 300;
    color: var(--grey-text);
  }
  .contact li {
    display: flex;
    align-items: center;
    gap: 7px;
    line-height: 1.5;
  }
  .contact svg { width: 10px; height: 10px; fill: var(--brand-green); }
  .mark-area {
    position: absolute;
    right: 36px;
    top: 42px;
    width: 226px;
    height: 226px;
    border-radius: 50%;
    background: var(--ink);
  }
</style>
</head>
<body>
<main class="stage">
  <section class="card card-front">
    <div class="front-info">
      <div class="brand">
        <span class="brand-dot"></span>
        <span class="brand-name">BrimFalcon</span>
      </div>
      <p class="tagline">Performance Driven EVs</p>
      <p class="person-name">DARA QUILL</p>
      <p class="person-role">President &amp; CEO</p>
      <p class="address">Westmere, Plainsland<br>Northaven</p>
      <ul class="contact">
        <li><svg viewBox="0 0 10 10"><path d="M2 0h2l1 3-1.5 1a6 6 0 0 0 2.5 2.5L7 5l3 1v2a2 2 0 0 1-2 2A8 8 0 0 1 0 2a2 2 0 0 1 2-2z"/></svg>555.010.2650</li>
        <li><svg viewBox="0 0 10 10"><path d="M0 2h10v6H0z M0 2l5 3.5L10 2" stroke="#fff" stroke-width="0.8"/></svg>dara@brimfalcon-example.com</li>
        <li><svg viewBox="0 0 10 10"><circle cx="5" cy="5" r="5"/></svg>www.brimfalcon-example.com</li>
      </ul>
    </div>
    <div class="mark-area" role="img" aria-label="Large brand symbol area"></div>
  </section>

  <section class="card card-back">
    <div class="brand">
      <span class="brand-dot"></span>
      <span class="brand-name">BrimFalcon</span>
    </div>
  </section>
</main>
</body>
</html>
```